Chimney Service company needs new business card design

We need a updated business card with our new logo added. We provide a full range of chimney services throughout Vermont and New Hampshire. The business card will be one sided and color. Attached is our current business card another document showing all the information we would like on the card.
We dont like a lot of flashy colors.... here is a link to our website to get an idea of our branding www.flueguardianvt.example

Target Market(s)

homeowners

Industry/Entity Type

Business

Contact Information for Business Card

See attached sheet for content.

Font styles to use
Serif
Sans Serif

Requirements
Must have
• all information provided on separate sheet
Should not have
• Additional information that may clogg up design

```html
<!DOCTYPE html>
<html lang="en">
<head>
<meta charset="utf-8">
<title>Flue Guardian – Business Card</title>
<link href="https://fonts.googleapis.com/css2?family=Cinzel:wght@400;700&family=Open+Sans:wght@400;600&display=swap" rel="stylesheet">
<style>
  :root {
    --brand-red: #a01c20;
    --ink: #2b2b2b;
    --paper: #ffffff;
    --backdrop: #e6e4e1;
  }
  * { box-sizing: border-box; margin: 0; padding: 0; }
  html, body { width: 1200px; height: 930px; overflow: hidden; }
  body { background: var(--backdrop); position: relative; font-family: "Open Sans", sans-serif; }

  .card {
    position: absolute;
    width: 720px;
    height: 411px;
    left: 240px;
    border-radius: 18px;
    overflow: hidden;
    box-shadow: 0 4px 14px rgba(0,0,0,.12);
  }
  .card--front { top: 34px; background: var(--brand-red); }
  .card--back { top: 485px; background: var(--paper); }

  /* front */
  .front-mark {
    position: absolute; inset: 0;
    display: flex; align-items: center; justify-content: center; gap: 22px;
  }
  .front-mark__square { width: 64px; height: 64px; border: 6px solid var(--paper); }
  .front-mark__name {
    font-family: "Cinzel", serif; font-weight: 400; font-size: 40px;
    color: var(--paper); letter-spacing: 1px;
  }

  /* back */
  .brand {
    position: absolute; left: 40px; top: 46px; width: 310px;
    display: flex; flex-direction: column; align-items: center; gap: 22px;
  }
  .brand__square { width: 118px; height: 118px; border: 9px solid var(--ink); }
  .brand__name {
    font-family: "Cinzel", serif; font-weight: 400; font-size: 32px;
    color: var(--ink); letter-spacing: 1px; white-space: nowrap;
  }
  .divider {
    position: absolute; left: 380px; top: 40px; width: 2px; height: 220px;
    background: var(--brand-red);
  }
  .details { position: absolute; left: 408px; top: 36px; width: 300px; }
  .contact { list-style: none; margin-bottom: 14px; }
  .contact li {
    display: flex; align-items: center; gap: 10px;
    font-size: 14.5px; color: var(--ink); line-height: 24px;
  }
  .contact svg { width: 13px; height: 13px; flex: none; fill: var(--brand-red); }
  .services__title {
    font-family: "Cinzel", serif; font-weight: 700; font-size: 19px;
    color: var(--brand-red); margin-bottom: 4px;
  }
  .services__list { list-style: none; }
  .services__list li { font-size: 14.5px; color: var(--ink); line-height: 21px; }

  .service-area {
    position: absolute; left: 0; right: 0; top: 312px; text-align: center;
    font-family: "Cinzel", serif; font-size: 15px; color: var(--ink); letter-spacing: .5px;
  }
  .service-area__since { font-family: "Open Sans", sans-serif; color: var(--brand-red); }
  .promise-band {
    position: absolute; left: 0; right: 0; bottom: 0; height: 56px;
    background: var(--brand-red);
    display: flex; align-items: center; justify-content: center;
    font-family: "Cinzel", serif; font-size: 17px; color: var(--paper); letter-spacing: .5px;
  }
</style>
</head>
<body>

<section class="card card--front" aria-label="Card front">
  <div class="front-mark">
    <span class="front-mark__square"></span>
    <span class="front-mark__name">Flue Guardian</span>
  </div>
</section>

<section class="card card--back" aria-label="Card back">
  <div class="brand">
    <span class="brand__square"></span>
    <span class="brand__name">Flue Guardian</span>
  </div>

  <div class="divider"></div>

  <div class="details">
    <ul class="contact">
      <li>
        <svg viewBox="0 0 24 24" aria-hidden="true"><path d="M6.6 10.8a15.1 15.1 0 0 0 6.6 6.6l2.2-2.2a1 1 0 0 1 1-.25 11.4 11.4 0 0 0 3.6.57 1 1 0 0 1 1 1V20a1 1 0 0 1-1 1A17 17 0 0 1 3 4a1 1 0 0 1 1-1h3.5a1 1 0 0 1 1 1c0 1.25.2 2.45.57 3.57a1 1 0 0 1-.25 1z"/></svg>
        802-555-0147
      </li>
      <li>
        <svg viewBox="0 0 24 24" aria-hidden="true"><path d="M2 5h20v14H2z M2 5l10 8 10-8" fill="none" stroke="#a01c20" stroke-width="2.5"/></svg>
        info@flueguardianvt.example
      </li>
      <li>
        <svg viewBox="0 0 24 24" aria-hidden="true"><circle cx="12" cy="12" r="10" fill="none" stroke="#a01c20" stroke-width="2.5"/><path d="M2 12h20M12 2c3 3 3 17 0 20M12 2c-3 3-3 17 0 20" fill="none" stroke="#a01c20" stroke-width="2"/></svg>
        www.flueguardianvt.example
      </li>
    </ul>
    <div class="services">
      <h2 class="services__title">Services We Provide</h2>
      <ul class="services__list">
        <li>Full Masonry Services</li>
        <li>Historic chimney restoration</li>
        <li>Stainless steel liners</li>
        <li>New Chimney installations</li>
        <li>VTHG Certified Chimney sweeps</li>
      </ul>
    </div>
  </div>

  <p class="service-area">Serving VT and New Hampshire–<span class="service-area__since">since 1989</span></p>

  <div class="promise-band">Fully Insured–Free Estimates | Family Owned and Operated</div>
</section>

</body>
</html>
```